design a construction company business card

Design business card around our logo. Card must have all the typical info: name, title, address, phone, email, business name, etc. Somewhere on the card I would like to see our motto "Grounded in trust... Driven by dedication." Consider adding a splash of bright orange to the card to complement the blues and silvers/grays in the logo. We are open to metallic inks, textures, etc. We would like to see options on both light and dark backgrounds. The font in the logo is Euro Technic Extended Regular.

```html
<!DOCTYPE html>
<html lang="en">
<head>
<meta charset="utf-8">
<title>Harlow Contracting – Business Card</title>
<link rel="stylesheet" href="https://fonts.googleapis.com/css2?family=Michroma&family=Roboto+Condensed:ital,wght@0,700;1,700&display=swap">
<style>
  :root {
    --bg: #e9e7e3;
    --blue-deep: #2540a8;
    --blue-mid: #2f55c4;
    --blue-bright: #1c8fd6;
    --silver-light: #f7f7f7;
    --silver-mid: #d9d9d9;
    --gray-band: #9a9a9a;
    --gray-text: #e6e6e6;
    --white: #ffffff;
    --logo-blue: #2f63c8;
  }
  * { box-sizing: border-box; margin: 0; padding: 0; }
  html, body { width: 1200px; height: 780px; overflow: hidden; background: var(--bg); }
  .canvas { position: relative; width: 1200px; height: 780px; }

  .card { position: absolute; border-radius: 22px; overflow: hidden; box-shadow: 0 10px 30px rgba(0,0,0,.18); }

  /* Front */
  .card--front { left: 70px; top: 70px; width: 380px; height: 640px; background: linear-gradient(180deg, var(--white) 0%, var(--silver-light) 30%, var(--silver-mid) 42%); }
  .card__shapes { position: absolute; inset: 0; }
  .brand { position: absolute; left: 0; right: 0; top: 120px; text-align: center; font-family: "Michroma", sans-serif; color: var(--logo-blue); }
  .brand__name { font-size: 42px; letter-spacing: 2px; line-height: 1; }
  .brand__sub { font-size: 12.5px; letter-spacing: 2px; margin-top: 10px; }
  .brand__mark { display: inline-block; width: 10px; height: 10px; background: currentColor; margin-right: 10px; vertical-align: middle; }

  .contact { position: absolute; left: 0; right: 0; top: 328px; text-align: center; color: var(--white); font-family: "Michroma", sans-serif; }
  .contact__name { font-family: "Roboto Condensed", sans-serif; font-weight: 700; font-size: 24px; letter-spacing: 3px; text-transform: uppercase; }
  .contact__title { font-size: 14px; margin-top: 2px; }
  .contact__label { font-family: "Roboto Condensed", sans-serif; font-style: italic; font-weight: 700; font-size: 13px; margin-top: 12px; }
  .contact__value { font-size: 13px; }
  .contact__rule { width: 250px; height: 1px; background: rgba(255,255,255,.55); margin: 12px auto 0; }
  .contact__address { font-size: 12.5px; line-height: 1.55; margin-top: 12px; }
  .web { position: absolute; left: 0; right: 0; bottom: 22px; text-align: center; font-family: "Michroma", sans-serif; font-size: 14px; letter-spacing: 1.5px; color: var(--gray-text); }

  /* Back */
  .card--back { left: 510px; top: 200px; width: 620px; height: 380px; background: radial-gradient(ellipse at 70% 10%, var(--blue-bright) 0%, var(--blue-mid) 45%, var(--blue-deep) 100%); }
  .back__brand { position: absolute; left: 0; right: 0; top: 110px; text-align: center; font-family: "Michroma", sans-serif; color: var(--white); }
  .back__brand .brand__name { font-size: 56px; letter-spacing: 3px; }
  .back__brand .brand__sub { font-size: 15px; margin-top: 14px; }
  .motto { position: absolute; left: 0; right: 0; bottom: 64px; text-align: center; color: var(--white); font-family: "Roboto Condensed", sans-serif; font-style: italic; font-weight: 700; font-size: 19px; letter-spacing: 1px; }
</style>
</head>
<body>
<main class="canvas">
  <section class="card card--front" aria-label="Business card front">
    <svg class="card__shapes" width="380" height="640" viewBox="0 0 380 640" aria-hidden="true">
      <defs>
        <linearGradient id="blueBody" x1="0" y1="0" x2="0.4" y2="1">
          <stop offset="0" stop-color="#1c8fd6"/>
          <stop offset="0.5" stop-color="#2f55c4"/>
          <stop offset="1" stop-color="#2540a8"/>
        </linearGradient>
      </defs>
      <path d="M0 300 Q190 250 380 330 L380 640 L0 640 Z" fill="url(#blueBody)"/>
      <path d="M40 292 Q220 262 380 340" fill="none" stroke="#ffffff" stroke-width="3"/>
      <rect x="0" y="560" width="380" height="80" fill="#9a9a9a"/>
      <rect x="0" y="560" width="380" height="10" fill="#c9c9c9"/>
    </svg>
    <div class="brand">
      <div class="brand__name"><span class="brand__mark"></span>HARLOW</div>
      <div class="brand__sub">CONTRACTING, INC.</div>
    </div>
    <div class="contact">
      <div class="contact__name">Daniel Reyes</div>
      <div class="contact__title">Founder</div>
      <div class="contact__label">Phone:</div>
      <div class="contact__value">(555) 014-2387</div>
      <div class="contact__rule"></div>
      <div class="contact__label">Email:</div>
      <div class="contact__value">info@harlowbuild.com</div>
      <div class="contact__rule"></div>
      <div class="contact__address">PO Box 418, 7 Quarry Lane<br>Geelong</div>
    </div>
    <div class="web">www.HARLOWBUILD.com</div>
  </section>

  <section class="card card--back" aria-label="Business card back">
    <div class="back__brand">
      <div class="brand__name">HARLOW</div>
      <div class="brand__sub">CONTRACTING, INC.</div>
    </div>
    <p class="motto">Grounded in trust... Driven by dedication.</p>
  </section>
</main>
</body>
</html>
```